Business Card Design

Our Pharmacy Opens late - the last to close in Brisbane
over 30 years since opened.
Open from 7am - 11pm every day.
Next to Corbel 7 Day Medical Centre
Parking in front of shop
Sit with a pharmacist for every script - the best advice every time.
Private consulting room.
We have the medication that you need.
Wide range Home Health Care products.

Looking for a card that my (young) staff feel happy to hand out to people they they meet.
Updates

Hello Many thanks for your submissions I just need to clarify the costings for this project as per my updated brief Please confirm then we can proceed Many thanks Clive

Reason: due to the adjusted brief and query I have extended the deadline Many thanks for those that have submitted, I will choose the designer as soon as I understand the costings of the project, as per the message despatched today Regards clive

Target Market(s)

men and women 30-70

Industry/Entity Type

Business

Contact Information for Business Card

Meltons Pharmacy - Corbel
317 Galloway Rd
Corbel 4187
Last to Close
Open 7am - 11pm

Font styles to use
Sans Serif

Requirements
Must have
• each batch of 250 will have the following staff names

Doreen Vallow, Senior Pharmacist
Lucia Tomba, Pharmacist
Wu Lan, Pharmacist
Odalie Brunskill, Pharmacist
Greta Lounds, Retail Manager
Joy Mettrick, Marketing Manager
Clive Melton, Pharmacist Proprietor
Should not have
• Please advise if the cost of this job covers the 7 individualised business cards.

Each staff member needs their own card.

please advise

```html
<!DOCTYPE html>
<html lang="en">
<head>
<meta charset="utf-8">
<title>Meltons Pharmacy – Business Card</title>
<link rel="stylesheet" href="https://fonts.googleapis.com/css2?family=Open+Sans:wght@400;600;700&display=swap">
<style>
  :root {
    --backdrop: #e4e4e2;
    --card: #fbfbfb;
    --navy: #1f2a8c;
    --ink: #2b2f55;
    --accent-yellow: #e6e01c;
    --accent-yellow-light: #f3ef8a;
    --muted: #555555;
  }
  * { box-sizing: border-box; margin: 0; padding: 0; }
  html, body {
    width: 1200px;
    height: 1027px;
    overflow: hidden;
    background: var(--backdrop);
    font-family: "Open Sans", Arial, sans-serif;
  }
  .sheet {
    width: 1200px;
    height: 1027px;
    display: flex;
    flex-direction: column;
    align-items: center;
    justify-content: center;
    gap: 40px;
  }
  .card {
    position: relative;
    width: 820px;
    height: 469px;
    background: var(--card);
    box-shadow: 0 2px 10px rgba(0,0,0,0.12);
    overflow: hidden;
  }
  .brand {
    position: absolute;
    display: flex;
    align-items: center;
    gap: 18px;
    color: var(--navy);
    font-weight: 700;
    font-size: 46px;
    line-height: 1;
    letter-spacing: 0.5px;
    white-space: nowrap;
  }
  .brand-dot {
    width: 34px;
    height: 34px;
    border-radius: 50%;
    background: var(--accent-yellow);
    flex: none;
  }
  .card--back .brand {
    left: 50%;
    top: 50%;
    transform: translate(-50%, -50%);
  }
  .card--front .brand {
    right: 70px;
    top: 92px;
  }
  .accent-rule {
    position: absolute;
    left: 46px;
    top: 0;
    bottom: 0;
    width: 12px;
    display: flex;
    gap: 3px;
  }
  .accent-rule span {
    display: block;
    height: 100%;
    background: var(--accent-yellow);
  }
  .accent-rule span:first-child { width: 7px; }
  .accent-rule span:last-child { width: 2px; background: var(--accent-yellow-light); }
  .contact {
    position: absolute;
    left: 90px;
    bottom: 44px;
    color: var(--muted);
  }
  .staff-name {
    font-size: 26px;
    font-weight: 700;
    color: var(--navy);
    line-height: 1.2;
  }
  .staff-role {
    font-size: 18px;
    font-weight: 600;
    color: var(--ink);
    margin-bottom: 14px;
  }
  .contact-list { list-style: none; }
  .contact-list li {
    display: flex;
    align-items: center;
    gap: 12px;
    font-size: 18px;
    line-height: 1.5;
    white-space: nowrap;
  }
  .contact-list svg { width: 16px; height: 16px; flex: none; fill: var(--muted); }
  .hours strong { color: var(--navy); font-weight: 600; }
</style>
</head>
<body>
<main class="sheet">
  <section class="card card--back" aria-label="Card back">
    <div class="brand"><span class="brand-dot"></span>Meltons Pharmacy</div>
  </section>

  <section class="card card--front" aria-label="Card front">
    <div class="accent-rule"><span></span><span></span></div>
    <div class="brand"><span class="brand-dot"></span>Meltons Pharmacy</div>
    <div class="contact">
      <p class="staff-name">Doreen Vallow</p>
      <p class="staff-role">Senior Pharmacist</p>
      <ul class="contact-list">
        <li>
          <svg viewBox="0 0 16 16" aria-hidden="true"><path d="M8 1a5 5 0 0 0-5 5c0 4 5 9 5 9s5-5 5-9a5 5 0 0 0-5-5Zm0 7a2 2 0 1 1 0-4 2 2 0 0 1 0 4Z"/></svg>
          Meltons Pharmacy - Corbel, 317 Galloway Rd, Corbel 4187
        </li>
        <li>
          <svg viewBox="0 0 16 16" aria-hidden="true"><path d="M2 3h12v11H2Zm1.5 3v6.5h9V6Z"/></svg>
          Next to Corbel 7 Day Medical Centre
        </li>
        <li class="hours">
          <svg viewBox="0 0 16 16" aria-hidden="true"><circle cx="8" cy="8" r="6.5" fill="none" stroke="#555" stroke-width="1.5"/><path d="M8 4v4.5l3 1.8" fill="none" stroke="#555" stroke-width="1.5"/></svg>
          <span><strong>Last to Close</strong> · Open 7am - 11pm</span>
        </li>
      </ul>
    </div>
  </section>
</main>
</body>
</html>
```